Suds & Woofs 2nd Annual Fundraiser

I am a Realtor sponsoring the 2nd annual fundraiser on behalf of Allies of Cedar Hollow Animal Haven. Like the flyer to be professional yet fun and inviting. Please see the attached file below. The 1st annual flyer was fun but not as professional, modern or inviting as I would have liked it to be.
Target Market(s)
Dog lovers in Ponte Vedra, Ponte Vedra Beach and Nocatee Florida
Logo Text
Needed
Font styles to use
Other font styles liked:
- Font that fits the style of the fundraiser
Colors
886aae
abd036
Requirements
Must have
- Please see the attached flyer and photos.
- This will be the 2nd Annual on Saturday, April 27, 2019 from 10AM - 1PM. Same location: Pemberly Realty, 418 Harrowgate Ln. Ponte Vedra FL 32940

```html
<!DOCTYPE html>
<html lang="en">
<head>
<meta charset="utf-8">
<title>Suds &amp; Woofs Doggie Wash Extravaganza</title>
<link href="https://fonts.googleapis.com/css2?family=Fredoka:wght@500;600&family=Pathway+Gothic+One&family=Signika:wght@400;500&family=Tinos&display=swap" rel="stylesheet">
<style>
  :root {
    --purple: #886aae;
    --purple-deep: #7a5aa3;
    --green: #abd036;
    --green-deep: #78b41e;
    --ink: #111111;
    --paper: #f6f8fa;
    --page: #f0efec;
    --muted: #3a3a3a;
  }
  * { margin: 0; padding: 0; box-sizing: border-box; }
  html, body { width: 1200px; height: 1200px; overflow: hidden; background: var(--page); }
  .flyer {
    position: absolute; left: 190px; top: 15px; width: 820px; height: 1170px;
    background: radial-gradient(ellipse at 45% 55%, #ffffff 0%, var(--paper) 60%, #e9eef2 100%);
    overflow: hidden;
  }
  .flyer__shapes { position: absolute; inset: 0; }
  .abs { position: absolute; }
  .ring { position: absolute; border-radius: 50%; background: #fff; }
  .ring--annual { left: 28px; top: 33px; width: 170px; height: 170px; border: 8px solid var(--purple); }
  .ring--title { left: 113px; top: 85px; width: 368px; height: 368px; border: 10px solid var(--green); }
  .ring--photo {
    left: 413px; top: 33px; width: 378px; height: 378px; border: 8px solid var(--purple);
    background: radial-gradient(circle at 50% 40%, #e8c9a0 0%, #d9b184 28%, #8fb84a 55%, #5f8f2a 100%);
  }
  .ring--badge {
    left: 554px; top: 403px; width: 188px; height: 188px; border: 6px solid var(--purple);
    display: flex; align-items: center; justify-content: center; text-align: center; padding: 0 22px;
    font-family: "Pathway Gothic One", sans-serif; font-size: 27px; line-height: 31px; color: var(--ink);
  }
  .annual {
    left: 28px; top: 70px; width: 170px; text-align: center;
    font-family: "Fredoka", sans-serif; font-weight: 600; color: var(--purple); font-size: 38px; line-height: 48px;
  }
  .title { font-family: "Fredoka", sans-serif; font-weight: 600; text-align: center; width: 368px; left: 118px; }
  .title--green { color: var(--green); font-size: 62px; line-height: 68px; top: 132px; }
  .title--purple { color: var(--purple); font-size: 46px; line-height: 54px; top: 272px; }
  .headline { left: 50px; top: 474px; width: 500px; text-align: center; font-family: "Fredoka", sans-serif; font-weight: 600; font-size: 30px; color: var(--ink); }
  .support { left: 0; width: 580px; top: 514px; text-align: center; font-family: "Pathway Gothic One", sans-serif; font-size: 34px; color: var(--ink); }
  .beneficiary { left: 33px; top: 552px; font-family: "Pathway Gothic One", sans-serif; font-size: 34px; color: var(--ink); letter-spacing: .3px; }
  .rule { left: 74px; width: 592px; height: 2px; background: var(--purple); }
  .details { left: 170px; top: 614px; font-family: "Signika", sans-serif; font-size: 25px; line-height: 32.5px; color: var(--ink); }
  .details__row { display: flex; }
  .details__label { width: 100px; }
  .features {
    left: 69px; top: 775px; width: 700px; display: grid; grid-template-columns: 406px 294px; row-gap: 12px;
    font-family: "Pathway Gothic One", sans-serif; font-size: 32px; color: var(--ink); list-style: none;
  }
  .features li { display: flex; align-items: center; gap: 10px; line-height: 38px; }
  .features svg { width: 30px; height: 30px; flex: none; }
  .donate { left: 33px; top: 935px; display: flex; align-items: center; gap: 12px; font-family: "Pathway Gothic One", sans-serif; font-size: 30px; color: var(--purple); }
  .pill { background: var(--purple); color: #fff; border-radius: 18px; padding: 0 14px; line-height: 38px; }
  .notes { left: 0; width: 820px; top: 982px; text-align: center; font-family: "Fredoka", sans-serif; font-weight: 500; font-size: 19px; line-height: 28px; color: var(--ink); }
  .notes em { font-style: normal; color: var(--purple); }
  .sponsor-name { left: 105px; top: 1096px; width: 130px; text-align: center; font-family: "Signika", sans-serif; font-size: 18px; line-height: 22px; color: var(--purple-deep); white-space: nowrap; }
  .contact { font-family: "Tinos", serif; font-size: 13px; line-height: 16px; color: var(--muted); }
  .contact--left { left: 240px; top: 1078px; }
  .contact--right { left: 560px; top: 1078px; }
  .divider { left: 451px; top: 1073px; width: 1px; height: 75px; background: var(--muted); }
  .mini-badge { left: 462px; top: 1086px; width: 88px; text-align: center; font-family: "Pathway Gothic One", sans-serif; font-size: 15px; line-height: 17px; color: var(--ink); }
</style>
</head>
<body>
<main class="flyer">
  <svg class="flyer__shapes" viewBox="0 0 820 1170" aria-hidden="true">
    <path d="M0 0 H560 C520 40 430 50 360 45 C250 38 150 80 110 150 C80 200 40 240 0 255 Z" fill="var(--green-deep)"/>
    <path d="M0 0 H470 C430 25 360 30 290 30 C180 32 110 70 70 130 C50 160 25 180 0 190 Z" fill="var(--green)"/>
    <path d="M820 0 V350 C790 300 760 250 745 200 C730 140 730 80 770 0 Z" fill="var(--purple)"/>
    <path d="M0 375 C20 380 25 420 20 470 C15 510 0 515 0 515 Z" fill="var(--purple)"/>
    <path d="M0 640 C40 660 60 720 55 800 C50 880 60 1000 120 1060 C145 1090 150 1130 140 1170 H0 Z" fill="var(--green-deep)"/>
    <path d="M0 680 C30 710 40 760 35 820 C30 900 40 990 90 1060 C110 1090 110 1130 95 1170 H0 Z" fill="var(--green)"/>
    <path d="M820 745 C760 800 720 870 740 960 C755 1030 720 1090 640 1130 C600 1150 580 1170 560 1170 H820 Z" fill="var(--green-deep)"/>
    <path d="M820 800 C780 850 760 910 775 980 C790 1050 760 1110 690 1170 H820 Z" fill="var(--green)"/>
  </svg>

  <div class="ring ring--photo" role="img" aria-label="Photo of a fluffy apricot puppy covered in soap suds sitting in a metal wash tub on green grass"></div>
  <div class="ring ring--title"></div>
  <div class="ring ring--annual"></div>
  <p class="ring ring--badge">Allies of Cedar Hollow Animal Haven</p>

  <p class="abs annual">2nd<br>Annual</p>
  <h1 class="abs title title--green">Suds<br>&amp; Woofs</h1>
  <p class="abs title title--purple">Doggie Wash<br>Extravaganza</p>

  <p class="abs headline">A family fun Event for All Ages</p>
  <p class="abs support">In Support of ;</p>
  <p class="abs beneficiary">ALLIES OF CEDAR HOLLOW ANIMAL HAVEN</p>

  <div class="abs rule" style="top:602px"></div>
  <div class="abs details">
    <div class="details__row"><span class="details__label">Date</span><span>: Saturday, April 27, 2019</span></div>
    <div class="details__row"><span class="details__label">Time</span><span>: 10AM - 1PM</span></div>
    <div class="details__row"><span class="details__label">Location</span><span>: Pemberly Realty, 418 Harrowgate Ln.</span></div>
    <div class="details__row"><span class="details__label"></span><span>&nbsp;&nbsp;Ponte Vedra FL 32940</span></div>
  </div>
  <div class="abs rule" style="top:749px"></div>

  <svg width="0" height="0" style="position:absolute">
    <symbol id="paw" viewBox="0 0 30 30">
      <g fill="none" stroke="var(--purple)" stroke-width="1.8">
        <ellipse cx="16" cy="19" rx="7" ry="6"/>
        <ellipse cx="6" cy="13" rx="3" ry="4"/>
        <ellipse cx="11" cy="6" rx="3" ry="4"/>
        <ellipse cx="19" cy="5" rx="3" ry="4"/>
        <ellipse cx="25" cy="11" rx="3" ry="4"/>
      </g>
    </symbol>
  </svg>
  <ul class="abs features">
    <li><svg><use href="#paw"/></svg>FREE Doggie Wash Raffle</li>
    <li><svg><use href="#paw"/></svg>Drawings</li>
    <li><svg><use href="#paw"/></svg>Food &amp; Beverages</li>
    <li><svg><use href="#paw"/></svg>Grand Prize</li>
    <li><svg><use href="#paw"/></svg>Vendors (FREE give-a-ways)</li>
    <li><svg><use href="#paw"/></svg>Donations Welcome</li>
  </ul>

  <div class="abs donate">
    <span>To make a donation:</span>
    <span class="pill">https://www.pawsupport.org/achah/</span>
    <span>click:</span>
    <span class="pill">Donate</span>
  </div>

  <p class="abs notes">All domestic breeds from puppies to seniors invited.<br>Please be sure <em>furry fido</em> is tolerant of other dogs, crowds and bathing.</p>

  <p class="abs sponsor-name">Pemberly Realty</p>
  <p class="abs contact contact--left">Marion Delacroix<br>Pemberly Realty Corp.<br>555.014.2231<br>marion@pemberlyrealtycorp.com</p>
  <div class="abs divider"></div>
  <p class="abs mini-badge">Allies of Cedar Hollow Animal Haven</p>
  <p class="abs contact contact--right">Rhea Caldwell<br>ACHAH<br>555.019.4470<br>rhea.caldwell@mailhub.net</p>
</main>
</body>
</html>
```